Etikett für Likörflasche - Tinderbox
Zielgruppe
Wir sind eine kleine Tinderbox / Likörmanufaktur. Unser Obst für die Brände und Liköre stammt aus eigenem Anbau bzw. von umliegenden regionalen Bauern. Hier setzen wir auf sehr gute Qualität und verwenden keine Zusatzstoffe, Geschmacksverstärker, Farbstoffe etc. Im ersten Schritt werden wir nur 3-4 verschiedene Liköre anbieten.
Wir möchten unsere Liköre zukünftig auf Veranstaltungen / Events und Märkten verkaufen. Hierfür suchen wir ein pfiffiges und ansprechendes Etikettendesign.
Das Wort 'Tinderbox' soll die Leute auf den Events zu uns führen. Das wird auch mit großen Fahnen am Verkaufsstand beworben. Da wir auch ein paar amerikanische Foodtrucks haben soll auch das Etikett ein bisschen amerikanisch gehalten werden.
Zielgruppe: 28 bis 55 Jahre (Männer & Frauen)
Verkaufspreis pro 0,5 Liter Flasche ca. 24,50 Euro
Aufgabenstellung
Es soll ein Etikett auf die Flasche (nur vorne nicht auf die Rückseite).
Etikettengröße: ca. 7,0 x 8,5cm (für die 0,5l Flasche)
Angaben die sich auf dem Etikett ändern:
- Inhalt entweder 0,35l oder 0,5l Flasche
- Bezeichnung vom Inhalt und 'Kurzbeschreibung'
- Alkoholgehalt
Ich habe in PowerPoint schon mal ein Etikett zusammen gestellt, auf dem die Angaben alle mit enthalten sind. Hier fehlt mir allerdings der Pfiff und das Professionelle. Auch die Darstellung der Eigenschaften wie 'Echte Früchte', 'Handcrafted' etc. gefällt mir so auch nicht. Vielleicht wäre auch noch ein cooler Spruch darauf gut.
In die Anlage habe ich meine kreierte PowerPoint Folie gepackt (auf der 2. Folie findet ihr die geplante Flasche in die abgefüllt wird). Die zweite Datei ist ein Design was meinen Vorstellungen schon gut nahe kommt aus dem Internet (hier gefallen mir die Linien, kleine Gimmicks etc. da passiert einfach was auf dem Etikett). Von der Art her würde mir dieser Style gut gefallen. Es soll nur nicht zu überladen und kitschig werden.
Likörsorten die es geben wird: Wir werden uns erstmal auf 3-4 Sorten beschränken.

```html
<!DOCTYPE html>
<html lang="de">
<head>
<meta charset="utf-8">
<title>Hollin's Tinderbox – Etiketten</title>
<link href="https://fonts.googleapis.com/css2?family=Bebas+Neue&family=Caveat:wght@500&family=Special+Elite&family=Zilla+Slab:wght@500;700&family=Josefin+Sans:wght@400&display=swap" rel="stylesheet">
<style>
  :root {
    --bg: #f2f2f0;
    --sky: #bcdced;
    --navy: #243746;
    --cream: #ebe5d6;
    --cream-dark: #ddd5c2;
    --red: #c8143c;
    --ink: #2a3540;
    --light: #efe9dc;
  }
  * { box-sizing: border-box; margin: 0; padding: 0; }
  html, body { width: 882px; height: 1200px; overflow: hidden; background: var(--bg); }
  .sheet { position: relative; width: 882px; height: 1200px; }
  .variants-column { position: absolute; left: 598px; top: 0; width: 284px; height: 1200px; background: var(--sky); }

  .neck-strip {
    position: absolute; left: 272px; top: 60px; width: 58px; height: 230px;
    background: var(--red); display: flex; flex-direction: column; align-items: center; padding-top: 22px; gap: 16px;
  }
  .neck-strip .brand-vertical {
    writing-mode: vertical-rl; font-family: "Bebas Neue", sans-serif; font-size: 34px;
    letter-spacing: 8px; color: var(--light);
  }
  .neck-strip .dot { width: 14px; height: 14px; border-radius: 50%; background: var(--light); }

  .label-main { position: absolute; left: 50px; top: 300px; }
  .mini { position: absolute; left: 29px; width: 225px; height: 288px; }
  .mini .label { transform: scale(.45); transform-origin: top left; }
  .mini-cherry { top: 60px; }
  .mini-peachy { top: 456px; }
  .mini-apple { top: 852px; }

  .label { width: 500px; height: 640px; display: flex; flex-direction: column; }
  .label-arch {
    height: 180px; margin: 0 14px; background: var(--navy);
    border-radius: 50% 50% 0 0 / 100% 100% 0 0;
    display: flex; flex-direction: column; align-items: center; justify-content: flex-end; padding-bottom: 18px;
  }
  .brand-name { font-family: "Bebas Neue", sans-serif; color: var(--light); text-align: center; line-height: .9; }
  .brand-name .owner { display: block; font-size: 40px; letter-spacing: 2px; }
  .brand-name .house { display: block; font-size: 66px; letter-spacing: 3px; }

  .label-body {
    flex: 1; background: radial-gradient(ellipse at 50% 40%, var(--cream) 55%, var(--cream-dark) 100%);
    padding: 18px 24px 0; display: flex; flex-direction: column; align-items: center; color: var(--ink);
  }
  .claims { display: grid; grid-template-columns: 1fr auto 1fr; width: 100%; align-items: center; height: 72px; }
  .claims .script { font-family: "Caveat", cursive; font-size: 22px; text-align: center; }
  .claims .motto {
    font-family: "Special Elite", monospace; font-size: 19px; line-height: 1.35; text-align: center;
    border-left: 1.5px solid var(--ink); border-right: 1.5px solid var(--ink); padding: 4px 22px;
  }
  .title {
    margin-top: 22px; height: 92px; display: flex; align-items: center; justify-content: center;
    color: var(--red); font-family: "Zilla Slab", serif; font-weight: 700;
    font-size: 48px; line-height: 1; white-space: nowrap; letter-spacing: .5px;
  }
  .tagline { margin-top: 12px; font-family: "Zilla Slab", serif; font-weight: 500; font-size: 15.5px; text-align: center; line-height: 1.3; letter-spacing: .3px; }
  .features { display: grid; grid-template-columns: repeat(3, 1fr); width: 100%; margin-top: 10px; }
  .features > div, .facts > div { text-align: center; border-right: 1.5px solid var(--ink); }
  .features > div:last-child, .facts > div:last-child { border-right: 0; }
  .features > div { font-family: "Special Elite", monospace; font-size: 14px; line-height: 1.35; padding: 6px 0 10px; color: #4a5560; }
  .rule { width: 100%; height: 10px; display: block; }
  .facts { display: grid; grid-template-columns: repeat(3, 1fr); width: 100%; }
  .facts > div { font-family: "Zilla Slab", serif; font-weight: 700; font-size: 24px; padding: 8px 0 12px; }
  .label-footer {
    height: 56px; background: var(--navy); color: var(--light); font-family: "Josefin Sans", sans-serif;
    font-size: 11.5px; letter-spacing: 1.4px; text-align: center; display: flex; flex-direction: column; justify-content: center; gap: 3px;
  }
</style>
</head>
<body>
<main class="sheet">

  <div class="neck-strip">
    <span class="brand-vertical">HOLLINS</span>
    <span class="dot"></span>
  </div>

  <article class="label label-main">
    <header class="label-arch">
      <p class="brand-name"><span class="owner">HOLLIN'S</span><span class="house">Tinderbox</span></p>
    </header>
    <section class="label-body">
      <div class="claims">
        <span class="script">seasoned fruits</span>
        <span class="motto">THE ONE<br>&amp; ONLY</span>
        <span class="script">fully handcrafted</span>
      </div>
      <h1 class="title">RUSTY &amp; BERRY</h1>
      <p class="tagline">WILDE BEEREN TREFFEN AUF<br>VIELSCHICHTIGE NOTEN VON WHISKY UND KARAMELL</p>
      <div class="features"><div>NO<br>ADDITIVES</div><div>REAL<br>TASTE</div><div>100YEARS<br>EXPERIENCE</div></div>
      <svg class="rule" viewBox="0 0 452 10" preserveAspectRatio="none" aria-hidden="true">
        <line x1="4" y1="5" x2="448" y2="5" stroke="#2a3540" stroke-width="1.5"/>
        <path d="M4 5 L14 1 M4 5 L14 9 M448 5 L438 1 M448 5 L438 9" stroke="#2a3540" stroke-width="1.5" fill="none"/>
      </svg>
      <div class="facts"><div>500 ML</div><div>22%VOL.</div><div>44PROOF</div></div>
    </section>
    <footer class="label-footer">
      <span>HOLLIN'S TINDERBOX - AM LINDENHANG 12 - 91999 TALHEIM</span>
      <span>WWW.HOLLINS-TINDERBOX.DE</span>
    </footer>
  </article>

  <aside class="variants-column">
    <div class="mini mini-cherry">
      <article class="label">
        <header class="label-arch"><p class="brand-name"><span class="owner">HOLLIN'S</span><span class="house">Tinderbox</span></p></header>
        <section class="label-body">
          <div class="claims"><span class="script">seasoned fruits</span><span class="motto">THE ONE<br>&amp; ONLY</span><span class="script">fully handcrafted</span></div>
          <h2 class="title">RUSTY &amp; CHERRY</h2>
          <p class="tagline">WILDE BEEREN TREFFEN AUF<br>VIELSCHICHTIGE NOTEN VON WHISKY UND KARAMELL</p>
          <div class="features"><div>NO<br>ADDITIVES</div><div>REAL<br>TASTE</div><div>100YEARS<br>EXPERIENCE</div></div>
          <svg class="rule" viewBox="0 0 452 10" preserveAspectRatio="none" aria-hidden="true"><line x1="4" y1="5" x2="448" y2="5" stroke="#2a3540" stroke-width="1.5"/></svg>
          <div class="facts"><div>500 ML</div><div>22%VOL.</div><div>44PROOF</div></div>
        </section>
        <footer class="label-footer"><span>HOLLIN'S TINDERBOX - AM LINDENHANG 12 - 91999 TALHEIM</span><span>WWW.HOLLINS-TINDERBOX.DE</span></footer>
      </article>
    </div>

    <div class="mini mini-peachy">
      <article class="label">
        <header class="label-arch"><p class="brand-name"><span class="owner">HOLLIN'S</span><span class="house">Tinderbox</span></p></header>
        <section class="label-body">
          <div class="claims"><span class="script">seasoned fruits</span><span class="motto">THE ONE<br>&amp; ONLY</span><span class="script">fully handcrafted</span></div>
          <h2 class="title">RUSTY &amp; PEACHY</h2>
          <p class="tagline">WILDE BEEREN TREFFEN AUF<br>VIELSCHICHTIGE NOTEN VON WHISKY UND KARAMELL</p>
          <div class="features"><div>NO<br>ADDITIVES</div><div>REAL<br>TASTE</div><div>100YEARS<br>EXPERIENCE</div></div>
          <svg class="rule" viewBox="0 0 452 10" preserveAspectRatio="none" aria-hidden="true"><line x1="4" y1="5" x2="448" y2="5" stroke="#2a3540" stroke-width="1.5"/></svg>
          <div class="facts"><div>500 ML</div><div>22%VOL.</div><div>44PROOF</div></div>
        </section>
        <footer class="label-footer"><span>HOLLIN'S TINDERBOX - AM LINDENHANG 12 - 91999 TALHEIM</span><span>WWW.HOLLINS-TINDERBOX.DE</span></footer>
      </article>
    </div>

    <div class="mini mini-apple">
      <article class="label">
        <header class="label-arch"><p class="brand-name"><span class="owner">HOLLIN'S</span><span class="house">Tinderbox</span></p></header>
        <section class="label-body">
          <div class="claims"><span class="script">seasoned fruits</span><span class="motto">THE ONE<br>&amp; ONLY</span><span class="script">fully handcrafted</span></div>
          <h2 class="title">RUSTY &amp; APPLE</h2>
          <p class="tagline">WILDE BEEREN TREFFEN AUF<br>VIELSCHICHTIGE NOTEN VON WHISKY UND KARAMELL</p>
          <div class="features"><div>NO<br>ADDITIVES</div><div>REAL<br>TASTE</div><div>100YEARS<br>EXPERIENCE</div></div>
          <svg class="rule" viewBox="0 0 452 10" preserveAspectRatio="none" aria-hidden="true"><line x1="4" y1="5" x2="448" y2="5" stroke="#2a3540" stroke-width="1.5"/></svg>
          <div class="facts"><div>500 ML</div><div>22%VOL.</div><div>44PROOF</div></div>
        </section>
        <footer class="label-footer"><span>HOLLIN'S TINDERBOX - AM LINDENHANG 12 - 91999 TALHEIM</span><span>WWW.HOLLINS-TINDERBOX.DE</span></footer>
      </article>
    </div>
  </aside>

</main>
</body>
</html>
```